Falkrin homes and renovations business card design.

Would like some new card designs utilizing my new logo that look professional. I am open to different colors on the logo or utilize the same ones we have. I like the original concept but would like to see some fresh ideas and build on what we have already done.

Target Market(s)

Custom home building industry, Real estate sales, Renovation projects.

Industry/Entity Type

Home Builder

Contact Information for Business Card

Falkrin Homes and Renovations
2871 96th Avenue
Frank, Alberta
T2R3W8
Home : 403- 718-4063 Cell: 403- 294-5170

My info is : Dax Falkrin, President and CEO
email: falkrinhomes@maildrop-example.net
Website: falkrinhomes-example.com
websit

Requirements
Must have
• Must Use my new logo design. I am open to different colors on the logo or utilize the same ones in the existing design. I can upload the original logo design if needed.

```html
<!DOCTYPE html>
<html lang="en">
<head>
<meta charset="utf-8">
<title>Falkrin Homes and Renovations – Business Card</title>
<link rel="stylesheet" href="https://fonts.googleapis.com/css2?family=Source+Sans+3:wght@400;600&display=swap">
<style>
  :root {
    --page-bg: #e9e7e4;
    --card-white: #ffffff;
    --card-black: #050505;
    --gold: #b88a35;
    --text-light: #ffffff;
  }
  * { box-sizing: border-box; margin: 0; padding: 0; }
  html, body {
    width: 1200px;
    height: 900px;
    overflow: hidden;
    background: var(--page-bg);
    font-family: "Source Sans 3", sans-serif;
  }
  .business-card {
    position: absolute;
    left: 144px;
    top: 169px;
    width: 913px;
    height: 563px;
    background: var(--card-white);
    box-shadow: 0 10px 30px rgba(0,0,0,0.18);
    overflow: hidden;
  }
  .brand-area {
    position: absolute;
    left: 0; top: 0;
    width: 100%;
    height: 319px;
    display: flex;
    align-items: center;
    justify-content: center;
    padding-top: 40px;
  }
  .brand-name {
    color: var(--gold);
    font-size: 40px;
    font-weight: 600;
    line-height: 1;
    text-align: center;
  }
  .gold-band {
    position: absolute;
    left: 0; top: 319px;
    width: 100%;
    height: 14px;
    background: var(--gold);
  }
  .contact-panel {
    position: absolute;
    left: 0; top: 333px;
    width: 100%;
    height: 230px;
    background: var(--card-black);
    color: var(--text-light);
  }
  .person {
    position: absolute;
    right: calc(913px - 391px);
    top: 54px;
    text-align: right;
  }
  .person-name {
    color: var(--gold);
    font-size: 33px;
    font-weight: 400;
    letter-spacing: 0.5px;
    line-height: 1.1;
  }
  .person-title {
    font-size: 23px;
    line-height: 1.4;
  }
  .person-address {
    font-size: 23px;
    line-height: 1.4;
    margin-top: 10px;
  }
  .divider {
    position: absolute;
    left: 418px;
    top: 56px;
    width: 2px;
    height: 143px;
    background: var(--gold);
  }
  .contact-list {
    position: absolute;
    left: 454px;
    top: 56px;
    list-style: none;
  }
  .contact-list li {
    display: flex;
    align-items: center;
    height: 33px;
    font-size: 23px;
    white-space: nowrap;
  }
  .contact-icon {
    width: 20px;
    height: 20px;
    margin-right: 16px;
    flex: none;
    fill: var(--gold);
  }
</style>
</head>
<body>
  <div class="business-card">
    <header class="brand-area">
      <h1 class="brand-name">Falkrin Homes and Renovations</h1>
    </header>

    <div class="gold-band"></div>

    <section class="contact-panel">
      <div class="person">
        <p class="person-name">DAX FALKRIN</p>
        <p class="person-title">President and CEO</p>
        <p class="person-address">2871 96th Avenue Frank,<br>Alberta T2R3W8</p>
      </div>

      <div class="divider"></div>

      <ul class="contact-list">
        <li>
          <svg class="contact-icon" viewBox="0 0 20 20" aria-hidden="true">
            <path d="M2 7c0-3 4-4 8-4s8 1 8 4v2h-4V7H6v2H2z"/>
            <path d="M5 10h10l2 7H3z"/>
          </svg>
          403- 718-4063
        </li>
        <li>
          <svg class="contact-icon" viewBox="0 0 20 20" aria-hidden="true">
            <path d="M6 1h8a1 1 0 0 1 1 1v16a1 1 0 0 1-1 1H6a1 1 0 0 1-1-1V2a1 1 0 0 1 1-1zm1 3v11h6V4zm3 12.2a.9.9 0 1 0 0 1.8.9.9 0 0 0 0-1.8z"/>
          </svg>
          403- 294-5170
        </li>
        <li>
          <svg class="contact-icon" viewBox="0 0 20 20" aria-hidden="true">
            <path d="M2 5h16v10H2z M2 5l8 6 8-6" stroke="#050505" stroke-width="1.4"/>
          </svg>
          falkrinhomes@maildrop-example.net
        </li>
        <li>
          <svg class="contact-icon" viewBox="0 0 20 20" aria-hidden="true">
            <circle cx="10" cy="10" r="8"/>
            <path d="M2 10h16M10 2c-3 3-3 13 0 16M10 2c3 3 3 13 0 16" stroke="#050505" stroke-width="1.2" fill="none"/>
          </svg>
          www.falkrinhomes-example.com
        </li>
      </ul>
    </section>
  </div>
</body>
</html>
```